business card for a massage therapy practice named 'Cedar and Willow Massage Studio'

I really need a trendy, yet easy on the eyes business card to complement my logo. Ideally with some gold or rose gold foil work.

My uploaded file of the logo I have in horizontal but I have a vertical version as well. Another color that is used in the website is a blush pink here and there. I'd like to see some trendy tropical leaves in the design.

```html
<!DOCTYPE html>
<html lang="en">
<head>
<meta charset="utf-8">
<title>Cedar and Willow Massage Studio — Business Card</title>
<link href="https://fonts.googleapis.com/css2?family=Work+Sans:wght@400;500&family=Playball&display=swap" rel="stylesheet">
<style>
  :root {
    --backdrop: #2b2b2d;
    --card: #161617;
    --card-edge: #222224;
    --silver: #c9c9cb;
    --silver-dark: #6e6e72;
    --white: #f2f2f2;
    --gold: #b99a63;
    --mint: #8fd3c0;
  }
  * { margin: 0; padding: 0; box-sizing: border-box; }
  html, body { width: 1200px; height: 900px; overflow: hidden; }
  body {
    background: var(--backdrop);
    font-family: "Work Sans", sans-serif;
    position: relative;
  }
  .card {
    position: absolute;
    left: 250px;
    width: 700px;
    height: 400px;
    background: linear-gradient(135deg, var(--card-edge), var(--card) 60%);
    box-shadow: 0 14px 30px rgba(0,0,0,.45);
  }
  .card--front { top: 40px; }
  .card--back { top: 470px; }

  .brand {
    color: var(--silver);
    font-weight: 500;
    letter-spacing: .06em;
    text-transform: uppercase;
  }
  .card--front .brand {
    position: absolute;
    top: 0; left: 0; right: 0; bottom: 0;
    display: flex;
    align-items: center;
    justify-content: center;
    gap: 18px;
    font-size: 28px;
  }
  .brand-dot {
    width: 26px; height: 26px;
    border-radius: 50%;
    background: var(--silver-dark);
    flex: none;
  }
  .card--back .brand {
    position: absolute;
    top: 44px; left: 48px;
    display: flex;
    align-items: center;
    gap: 12px;
    font-size: 17px;
    color: var(--white);
  }
  .card--back .brand-dot { width: 20px; height: 20px; background: var(--gold); }

  .holder {
    position: absolute;
    top: 112px; left: 56px;
    font-family: "Playball", cursive;
    font-size: 34px;
    color: var(--gold);
    letter-spacing: .02em;
  }
  .address {
    position: absolute;
    top: 178px; left: 66px;
    font-size: 16px;
    line-height: 24px;
    color: var(--white);
    font-style: normal;
  }
  .contacts {
    position: absolute;
    top: 262px; left: 48px;
    list-style: none;
    font-size: 17px;
    line-height: 26px;
    color: var(--white);
  }
  .contacts li { display: flex; align-items: center; gap: 10px; }
  .contacts svg { width: 13px; height: 13px; flex: none; }

  .emblem {
    position: absolute;
    top: 70px; right: 120px;
    width: 200px; height: 260px;
    border-radius: 50%;
    background: radial-gradient(circle at 40% 35%, #e6e6e8, var(--silver) 40%, var(--silver-dark) 100%);
  }
</style>
</head>
<body>
  <section class="card card--front">
    <div class="brand"><span class="brand-dot"></span>Cedar and Willow Massage Studio</div>
  </section>

  <section class="card card--back">
    <div class="brand"><span class="brand-dot"></span>Cedar and Willow Massage Studio</div>
    <p class="holder">Marisol Vega</p>
    <address class="address">418 Laurel Ave. suite 210,<br>Fairmont, CA 95620</address>
    <ul class="contacts">
      <li>
        <svg viewBox="0 0 16 16" aria-hidden="true"><path d="M4 1l3 3-2 2a9 9 0 005 5l2-2 3 3-2 3C7 15 1 9 1 3z" fill="var(--gold)"/></svg>
        (555) 214-7730
      </li>
      <li>
        <svg viewBox="0 0 16 16" aria-hidden="true"><rect x="1" y="3" width="14" height="10" fill="none" stroke="var(--gold)" stroke-width="1.5"/><path d="M1 3l7 6 7-6" fill="none" stroke="var(--gold)" stroke-width="1.5"/></svg>
        cedarandwillow@mail.com
      </li>
      <li>
        <svg viewBox="0 0 16 16" aria-hidden="true"><circle cx="8" cy="8" r="6.5" fill="none" stroke="var(--gold)" stroke-width="1.5"/><path d="M1.5 8h13M8 1.5c-3 3-3 10 0 13M8 1.5c3 3 3 10 0 13" fill="none" stroke="var(--gold)" stroke-width="1.2"/></svg>
        www.cedarandwillowstudio.com
      </li>
    </ul>
    <div class="emblem" role="img" aria-label="Large embossed silver foil brand emblem"></div>
  </section>
</body>
</html>
```